LM-Steuerberatung WordPress Site fully implemented (tax advisor)

Hello!
I need a little Wordpress Site for my newly founded Tax-Advisor Company.
I am a one-man Office advising in the area of Crypto-Currency.
PLEASE only provide a Design, if you can also Implement a WP-Site afterwards on an existing Webspace.

Please find the Content and Website-Description in the attached Document

Language for the Website is German (for now)

Target Market(s)

Tax-Advisory (specialized in Crypto Currency)

Coding

Coded - Design and coding required

Number of Pages Required

5+ page

Font styles to use
Sans Serif

Requirements
Must have
• Wordpress Implementation afterwards - Details according to attached Project Information Document

```html
<!DOCTYPE html>
<html lang="de">
<head>
<meta charset="utf-8">
<title>LM-Steuerberatung</title>
<link rel="stylesheet" href="https://fonts.googleapis.com/css2?family=Montserrat:wght@600;700&family=Mulish:wght@400;500&display=swap">
<style>
  :root {
    --navy-deep: #04112b;
    --navy: #0a2148;
    --navy-mid: #123566;
    --gold: #e5a800;
    --white: #ffffff;
    --text-soft: #f1f4fa;
  }
  * { box-sizing: border-box; margin: 0; padding: 0; }
  html, body { width: 1200px; height: 687px; overflow: hidden; }
  body {
    font-family: "Mulish", "Helvetica Neue", Arial, sans-serif;
    color: var(--white);
    background: var(--navy-deep);
  }
  .hero {
    position: relative;
    width: 1200px;
    height: 687px;
    overflow: hidden;
    background:
      radial-gradient(ellipse 60% 70% at 70% 40%, var(--navy-mid) 0%, transparent 70%),
      linear-gradient(160deg, var(--navy) 0%, var(--navy-deep) 75%);
  }
  .site-header {
    position: absolute;
    top: 24px; left: 111px; right: 113px;
    height: 38px;
    display: flex;
    align-items: center;
    justify-content: space-between;
  }
  .brand {
    display: flex;
    align-items: center;
    gap: 16px;
    font-family: "Montserrat", Arial, sans-serif;
    font-weight: 700;
    font-size: 16px;
    letter-spacing: 0.2px;
    color: var(--white);
    text-decoration: none;
  }
  .brand-mark { width: 31px; height: 31px; background: var(--white); }
  .main-nav { display: flex; gap: 36px; list-style: none; }
  .main-nav a {
    color: var(--white);
    text-decoration: none;
    font-size: 15px;
    font-weight: 500;
    display: inline-flex;
    align-items: center;
    gap: 4px;
  }
  .hero-illustration {
    position: absolute;
    left: 561px; top: 150px;
    width: 639px; height: 433px;
    background:
      radial-gradient(ellipse 30% 35% at 58% 62%, rgba(240, 181, 42, 0.55) 0%, transparent 100%),
      radial-gradient(ellipse 55% 60% at 60% 45%, rgba(40, 120, 190, 0.45) 0%, transparent 100%);
    border-radius: 12px;
  }
  .hero-content { position: absolute; left: 111px; top: 183px; width: 540px; }
  .hero-title {
    font-family: "Montserrat", Arial, sans-serif;
    font-weight: 700;
    font-size: 41px;
    line-height: 52px;
    color: var(--white);
  }
  .hero-lead {
    margin-top: 12px;
    font-size: 13.5px;
    line-height: 25px;
    color: var(--text-soft);
  }
  .cta-button {
    display: inline-flex;
    align-items: center;
    justify-content: center;
    margin-top: 19px;
    width: 274px; height: 50px;
    border-radius: 25px;
    background: var(--gold);
    color: var(--white);
    font-family: "Montserrat", Arial, sans-serif;
    font-weight: 600;
    font-size: 14px;
    text-decoration: none;
  }
  .idea-list {
    position: absolute;
    left: 111px; top: 485px;
    width: 600px;
    list-style: none;
  }
  .idea-list li {
    display: flex;
    gap: 9px;
    font-size: 14.6px;
    line-height: 23px;
    margin-bottom: 11px;
    white-space: nowrap;
    color: var(--text-soft);
  }
  .idea-icon { flex: 0 0 14px; margin-top: 5px; }
</style>
</head>
<body>
<main class="hero">
  <header class="site-header">
    <a class="brand" href="#"><span class="brand-mark"></span>LM STEUERBERATUNG</a>
    <ul class="main-nav">
      <li><a href="#">Home</a></li>
      <li><a href="#">Leistungen
        <svg width="9" height="6" viewBox="0 0 9 6"><path d="M0 0h9L4.5 6z" fill="#ffffff"/></svg></a></li>
      <li><a href="#">Über mich</a></li>
      <li><a href="#">Kontakt</a></li>
      <li><a href="#">Impressum</a></li>
    </ul>
  </header>

  <div class="hero-illustration" role="img" aria-label="Illustration: Smartphone vor einer digitalen Weltkarte mit einem Stapel goldener Krypto-Münzen und Kurscharts"></div>

  <section class="hero-content">
    <h1 class="hero-title">Willkommen bei LM<br>-Steuerberatung!</h1>
    <p class="hero-lead">Ihrem Spezialisten bei allen steuerlichen Themen rund um Einkün-<br>fte&amp;amp; Vermögen aus Krypto-Assets.</p>
    <a class="cta-button" href="#">Weiter zu unseren Leistungen</a>
  </section>

  <ul class="idea-list">
    <li><svg class="idea-icon" width="14" height="14" viewBox="0 0 14 14"><circle cx="7" cy="7" r="7" fill="#e5a800"/><path d="M4 7h5.5M7 4.5 9.5 7 7 9.5" stroke="#04112b" stroke-width="1.6" fill="none" stroke-linecap="round" stroke-linejoin="round"/></svg>
      <span>Dann mach ich eine Schweizer Holding-Gesellschaft– dort zahlt man<br>fast keine Steuern</span></li>
    <li><svg class="idea-icon" width="14" height="14" viewBox="0 0 14 14"><circle cx="7" cy="7" r="7" fill="#e5a800"/><path d="M4 7h5.5M7 4.5 9.5 7 7 9.5" stroke="#04112b" stroke-width="1.6" fill="none" stroke-linecap="round" stroke-linejoin="round"/></svg>
      <span>dann melde ich einfach meinen Hauptwohnsitz in Österreich ab</span></li>
    <li><svg class="idea-icon" width="14" height="14" viewBox="0 0 14 14"><circle cx="7" cy="7" r="7" fill="#e5a800"/><path d="M4 7h5.5M7 4.5 9.5 7 7 9.5" stroke="#04112b" stroke-width="1.6" fill="none" stroke-linecap="round" stroke-linejoin="round"/></svg>
      <span>Dann lass ich meine Kryptos auf einer Börse in Singapur, dort ist das steuerfrei</span></li>
  </ul>
</main>
</body>
</html>
```